Velmarotix - world unique technology for better life - please let them know who am i at first sight

We need a new business card for company which is a provider of unique crystal based technology suitable for all living being. For more information and final design you can use our brochure (our colours are black and blue from brochure).
We use Verdana font

Industry/Entity Type

Business

Contact Information for Business Card

regular dimension

Font styles to use
Other font styles liked:
• Verdana

Requirements
Must have
• Logo
• name
• function/position
• phone
• mobile
• e-mail
• adress
Nice to have
• inovative design (technology directed)

```html
<!DOCTYPE html>
<html lang="en">
<head>
<meta charset="utf-8">
<title>Velmarotix – Business Card</title>
<link href="https://fonts.googleapis.com/css2?family=Michroma&family=Montserrat:wght@200&family=Saira:wght@400;500&display=swap" rel="stylesheet">
<style>
  :root {
    --page-bg: #e9ecef;
    --card-white: #f4f5f6;
    --brand-blue: #05a3de;
    --wave-grey: #a5a8ab;
    --ink-dark: #2b2d30;
    --on-blue: #ffffff;
  }
  html, body {
    margin: 0;
    width: 1200px;
    height: 900px;
    overflow: hidden;
    background: var(--page-bg);
  }
  .stage {
    width: 1200px;
    height: 900px;
    display: flex;
    align-items: center;
    justify-content: center;
  }
  .business-card {
    position: relative;
    width: 900px;
    height: 514px;
    border-radius: 46px;
    overflow: hidden;
    background: var(--card-white);
    box-shadow: 0 10px 30px rgba(0,0,0,0.15);
  }
  .card-waves {
    position: absolute;
    inset: 0;
  }
  .brand {
    position: absolute;
    left: 62px;
    top: 110px;
    display: flex;
    align-items: center;
    gap: 22px;
  }
  .brand-dot {
    width: 92px;
    height: 92px;
    border-radius: 50%;
    background: var(--brand-blue);
  }
  .brand-name {
    font-family: "Montserrat", Verdana, sans-serif;
    font-weight: 200;
    font-size: 60px;
    letter-spacing: 2px;
    color: var(--brand-blue);
    text-transform: uppercase;
  }
  .holder {
    position: absolute;
    left: 184px;
    top: 262px;
  }
  .holder-name {
    font-family: "Michroma", Verdana, sans-serif;
    font-size: 21px;
    color: var(--ink-dark);
    text-transform: uppercase;
    margin: 0;
    line-height: 1.3;
  }
  .holder-role {
    font-family: "Saira", Verdana, sans-serif;
    font-weight: 500;
    font-size: 18px;
    color: var(--brand-blue);
    margin: 2px 0 0 40px;
  }
  .contact-list {
    position: absolute;
    right: 36px;
    top: 212px;
    list-style: none;
    margin: 0;
    padding: 0;
    font-family: "Saira", Verdana, sans-serif;
    font-size: 18px;
    color: var(--on-blue);
    text-align: right;
  }
  .contact-list li {
    display: flex;
    justify-content: flex-end;
    align-items: center;
    gap: 10px;
    height: 33px;
    letter-spacing: 1px;
  }
  .contact-list svg {
    width: 19px;
    height: 19px;
    fill: var(--on-blue);
  }
  .address {
    position: absolute;
    left: 44px;
    bottom: 40px;
    font-family: "Saira", Verdana, sans-serif;
    font-weight: 500;
    font-size: 22px;
    line-height: 1.45;
    letter-spacing: 1px;
    color: var(--on-blue);
    margin: 0;
  }
</style>
</head>
<body>
<main class="stage">
  <section class="business-card">
    <svg class="card-waves" viewBox="0 0 900 514" aria-hidden="true">
      <path d="M0,322 C140,392 300,412 460,377 C600,322 700,92 900,62" fill="none" stroke="var(--wave-grey)" stroke-width="12"/>
      <path d="M0,338 C140,408 300,428 460,393 C480,386 500,377 520,370 L520,514 L0,514 Z" fill="var(--wave-grey)"/>
      <path d="M0,350 C140,420 300,440 460,405 C600,350 700,120 900,90 L900,514 L0,514 Z" fill="var(--brand-blue)"/>
    </svg>

    <div class="brand">
      <span class="brand-dot"></span>
      <span class="brand-name">Velmarotix</span>
    </div>

    <div class="holder">
      <p class="holder-name">Daniel Moravec</p>
      <p class="holder-role">Managing Director</p>
    </div>

    <ul class="contact-list">
      <li>021 784 3190
        <svg viewBox="0 0 24 24"><path d="M6.6 10.8a15 15 0 0 0 6.6 6.6l2.2-2.2c.3-.3.7-.4 1-.2 1.1.4 2.3.6 3.6.6.6 0 1 .4 1 1V20c0 .6-.4 1-1 1A17 17 0 0 1 3 4c0-.6.4-1 1-1h3.5c.6 0 1 .4 1 1 0 1.3.2 2.5.6 3.6.1.3 0 .7-.2 1z"/></svg>
      </li>
      <li>021 784 3190
        <svg viewBox="0 0 24 24"><path d="M7 2h10a2 2 0 0 1 2 2v16a2 2 0 0 1-2 2H7a2 2 0 0 1-2-2V4a2 2 0 0 1 2-2zm0 3v13h10V5zm5 14.2a1 1 0 1 0 0 .1z"/></svg>
      </li>
      <li>021 784 3191
        <svg viewBox="0 0 24 24"><path d="M6 3h9l3 3v4h1a2 2 0 0 1 2 2v8a1 1 0 0 1-1 1H4a1 1 0 0 1-1-1v-8a2 2 0 0 1 2-2h1zm2 2v5h8V7h-2V5zm-1 8v2h2v-2zm4 0v2h2v-2zm4 0v2h2v-2zm-8 3v2h2v-2zm4 0v2h2v-2zm4 0v2h2v-2z"/></svg>
      </li>
      <li>contact@velmarotix.com
        <svg viewBox="0 0 24 24"><path d="M2 5h20v14H2zm2 2v.4l8 5.3 8-5.3V7zm0 2.8V17h16V9.8l-8 5.3z"/></svg>
      </li>
      <li>www.velmarotix.com
        <svg viewBox="0 0 24 24"><path d="M12 2a10 10 0 1 0 0 20 10 10 0 0 0 0-20zm6.9 9h-3a15 15 0 0 0-1.3-5.6A8 8 0 0 1 18.9 11zM12 4.1c.9 1.3 1.7 3.6 1.9 6.9h-3.8c.2-3.3 1-5.6 1.9-6.9zM9.4 5.4A15 15 0 0 0 8.1 11h-3a8 8 0 0 1 4.3-5.6zM5.1 13h3a15 15 0 0 0 1.3 5.6A8 8 0 0 1 5.1 13zm6.9 6.9c-.9-1.3-1.7-3.6-1.9-6.9h3.8c-.2 3.3-1 5.6-1.9 6.9zm2.6-1.3a15 15 0 0 0 1.3-5.6h3a8 8 0 0 1-4.3 5.6z"/></svg>
      </li>
    </ul>

    <p class="address">114.9th floor,Arcade<br>Harbour Lane RVT</p>
  </section>
</main>
</body>
</html>
```